Mira Ellsworth ADHD coach needs a flyer

I need a flyer to be sent by email. the copy is attached. It can be changed/reduced to fit the flyer. I would like to keep my website colors. My website is www.miraellsworth.net - Thank you!

```html
<!DOCTYPE html>
<html lang="en">
<head>
<meta charset="utf-8">
<title>Mira Ellsworth – ADHD and Academic Coach</title>
<link rel="stylesheet" href="https://fonts.googleapis.com/css2?family=Oswald:wght@200;300&family=Nunito+Sans:ital,wght@0,400;0,700;0,800;0,900;1,400&display=swap">
<style>
:root{
  --mist:#dce6eb;
  --slate:#a0b4bf;
  --name:#9db3bf;
  --ink:#2f3336;
  --text:#444a4e;
  --panel:#e1e8ec;
  --charcoal:#6b6d6f;
  --white:#ffffff;
}
*{margin:0;padding:0;box-sizing:border-box}
html,body{width:840px;height:1200px;overflow:hidden;background:var(--white)}
body{font-family:"Nunito Sans",Arial,sans-serif;color:var(--text);position:relative}
.block{position:absolute}
.brand{left:0;top:0;width:280px;height:140px;background:var(--mist);padding:18px 0 0 36px;overflow:hidden}
.brand-name{font-family:"Oswald",sans-serif;font-weight:200;font-size:62px;line-height:58px;color:var(--name);letter-spacing:0;white-space:nowrap;transform:scaleX(.8);transform-origin:left top}
.headline-band{left:280px;top:0;width:560px;height:140px;background:var(--slate);padding:30px 0 0 31px}
.headline{color:var(--white);font-weight:900;font-size:22.5px;line-height:28px;letter-spacing:.2px}
.headline-chevrons{position:absolute;left:346px;top:110px}
.credential{left:0;top:140px;width:280px;height:27px;padding:3px 0 0 39px;font-family:"Oswald",sans-serif;font-weight:300;font-size:15px;color:var(--ink)}
.photo{position:absolute}
.portrait{left:0;top:167px;width:280px;height:432px;background:linear-gradient(180deg,#b9c0c3 0%,#c7cbcc 40%,#e9d9d8 75%,#d9c3c4 100%)}
.group-photo{left:280px;top:372px;width:560px;height:227px;background:linear-gradient(180deg,rgba(230,236,228,0) 0%,#a9b89a 25%,#8b7a6a 60%,#6f5a49 85%,#8c8a86 100%)}
.intro{left:310px;top:165px;width:520px;display:flex;gap:34px;font-size:10.2px;line-height:13px;z-index:2}
.intro .col-a{width:216px}
.intro .col-b{width:246px}
.intro .lead{font-weight:800;color:var(--ink);margin-bottom:13px}
.divider-band{left:280px;top:599px;width:560px;height:23px;background:var(--panel)}
.focus{left:21px;top:612px;width:240px;font-size:9.4px;line-height:11.7px;color:var(--ink);z-index:3}
.section-title{font-weight:900;font-size:13px;letter-spacing:.3px;color:var(--ink)}
.section-sub{font-style:italic;font-size:13px;line-height:16px;color:var(--ink);letter-spacing:.2px}
.focus p{margin-top:10px}
.focus ul,.bullets{list-style:none}
.focus li,.bullets li{position:relative;padding-left:16px}
.focus li::before,.bullets li::before{content:"";position:absolute;left:2px;top:4.5px;width:3.5px;height:3.5px;border-radius:50%;background:var(--ink)}
.focus li{margin-top:2px}
.potential-head{left:280px;top:622px;width:280px;height:66px;background:var(--white);padding:9px 0 0 24px}
.potential-list{left:280px;top:688px;width:280px;height:82px;background:var(--panel);padding:8px 0 0 24px}
.bullets{font-size:9.3px;line-height:14.2px;color:var(--text)}
.small-head{font-weight:900;font-size:13px;color:var(--ink);letter-spacing:.2px}
.have-head{left:280px;top:770px;width:280px;height:26px;padding:5px 0 0 24px;background:var(--white)}
.have-list{left:280px;top:796px;width:280px;height:108px;background:linear-gradient(180deg,var(--panel),var(--white));padding:8px 12px 0 24px;z-index:2}
.have-list .bullets{line-height:12.2px}
.have-list li{margin-bottom:2px}
.parents-head{left:560px;top:622px;width:280px;height:32px;padding:10px 0 0 24px;background:var(--white)}
.parents-quotes{left:560px;top:654px;width:280px;height:116px;background:var(--panel);padding:9px 18px 0 24px}
.students-head{left:560px;top:770px;width:280px;height:26px;padding:5px 0 0 24px;background:var(--white)}
.students-quotes{left:560px;top:796px;width:280px;height:126px;background:linear-gradient(180deg,var(--white),var(--panel));padding:9px 16px 0 24px}
.quote{font-size:9.1px;line-height:11.7px;color:var(--text);margin-bottom:11px}
.quote cite{font-style:italic}
.quote em{font-style:italic}
.study-photo{left:0;top:904px;width:560px;height:265px;background:linear-gradient(180deg,#ffffff 0%,#eef1f2 14%,#d9dcdd 35%,#8c7f74 62%,#3f4a62 100%)}
.student-photo{left:560px;top:922px;width:280px;height:171px;background:linear-gradient(90deg,#dfe3e5 0%,#c9cfd2 50%,#6b6466 75%,#d5dade 100%)}
.next-steps{left:560px;top:1093px;width:280px;height:76px;background:var(--charcoal);color:var(--white);padding:9px 24px 0 48px}
.next-steps h3{font-weight:900;font-size:13.5px;margin-bottom:3px}
.next-steps p{font-size:10px;line-height:12.5px}
.next-steps strong{font-weight:800}
.next-chevron{position:absolute;left:16px;top:12px}
.footer{left:0;top:1169px;width:840px;height:31px;text-align:center;padding-top:9px;font-weight:800;font-size:11px;color:var(--slate);letter-spacing:.3px}
.left-chevrons{left:21px;top:604px;z-index:3}
</style>
</head>
<body>
<header class="block brand">
  <div class="brand-name">MIRA<br>ELLSWORTH</div>
</header>
<div class="block headline-band">
  <h1 class="headline">Helping Your Child with ADHD or<br>Other Learning Challenges Thrive<br>in College and Beyond</h1>
  <svg class="headline-chevrons" width="140" height="18" viewBox="0 0 140 18" fill="none" stroke="#ffffff" stroke-width="1.1">
    <polyline points="1,2 8,9 1,16"/><polyline points="11,2 18,9 11,16"/><polyline points="21,2 28,9 21,16"/><polyline points="31,2 38,9 31,16"/>
    <polyline points="51,2 58,9 51,16"/><polyline points="59,2 66,9 59,16"/><polyline points="67,2 74,9 67,16"/><polyline points="75,2 82,9 75,16"/>
    <polyline points="95,2 102,9 95,16"/><polyline points="105,2 112,9 105,16"/><polyline points="115,2 122,9 115,16"/><polyline points="125,2 132,9 125,16"/>
  </svg>
</div>
<div class="block credential">Ph.D. &nbsp;|&nbsp; ADHD and Academic Coach</div>

<div class="photo portrait" role="img" aria-label="Portrait of the coach, smiling, arms crossed, in a light pink blazer against a grey wall"></div>
<div class="photo group-photo" role="img" aria-label="Group of smiling college students sitting on a wooden bench outdoors with laptops and tablets"></div>

<section class="block intro">
  <div class="col-a">
    <p class="lead">Academic success coaching that leads to lifelong transformation for students with ADHD and similar challenges that may have impeded their ability to thrive.</p>
    <p>Sending your child off to college can feel scary, especially if that college is hundreds of miles away. You worry about how they'll do on their own—whether they'll make friends, earn good grades, and be happy—especially without you there to support them daily. You know your child is bright, and you want them to have a great future, but you're concerned they will struggle without the right support and resources.</p>
  </div>
  <div class="col-b">
    <p>You don't need to feel helpless as you send your child off to this next stage of their lives. Mira is dedicated to making that transition easier for everyone. Mira Ellsworth has years of experience helping students thrive despite their challenges. She sees your child's potential and helps them see it, too. She provides a safety net as they adjust to a new environment at college. Her services are comprehensive and adaptable, based on the requirements of each individual: helping with course selection and scheduling, time management, study strategies, focus, making new friends, and adapting to change. Through it all, Mira guides students through fundamental work on mindset to ensure that changes stick.</p>
  </div>
</section>

<div class="block divider-band"></div>

<div class="photo study-photo" role="img" aria-label="Four students gathered around a laptop, studying together with notes"></div>
<div class="photo student-photo" role="img" aria-label="Smiling student holding notebooks in front of library bookshelves"></div>

<svg class="block left-chevrons" width="200" height="18" viewBox="0 0 200 18" fill="none" stroke="#9db3bf" stroke-width="1.1">
  <polyline points="1,2 8,9 1,16"/><polyline points="11,2 18,9 11,16"/><polyline points="23,2 30,9 23,16"/><polyline points="33,2 40,9 33,16"/>
  <polyline points="55,2 62,9 55,16"/><polyline points="63,2 70,9 63,16"/><polyline points="71,2 78,9 71,16"/><polyline points="79,2 86,9 79,16"/>
  <polyline points="97,2 104,9 97,16"/><polyline points="107,2 114,9 107,16"/><polyline points="117,2 124,9 117,16"/><polyline points="127,2 134,9 127,16"/>
</svg>

<section class="block focus">
  <h2 class="section-title" style="margin-top:26px">EMPOWERING FOCUS:</h2>
  <div class="section-sub">HOW MIRA HELPS</div>
  <p>Mira has taken students from failing to a 3.0 GPA, and from a C student to the Dean's List, in just one semester. It doesn't take years to provide lasting results; all it takes is the right guide.</p>
  <p style="margin-top:8px">Uniquely positioned to help your child, Mira:</p>
  <ul>
    <li>Tailors support so that your child improves focus and maximizes their potential in college and beyond.</li>
    <li>Understands your child's unique needs - she sees the gifts that others often miss.</li>
    <li>Knows the academic landscape intimately, including the challenges faced by students with ADHD and other conditions.</li>
    <li>Helps with the logistics of scheduling in a way that most advisors can't, enrolling students in the courses that best suit their learning style.</li>
    <li>Nurtures the brilliance in your bright child.</li>
    <li>Provides a balance between encouraging students and challenging them.</li>
  </ul>
</section>

<section class="block potential-head">
  <h2 class="section-title">REALIZING POTENTIAL:</h2>
  <div class="section-sub">THE TRANSFORMATION YOU'LL SEE<br>IN YOUR CHILD</div>
</section>
<div class="block potential-list">
  <ul class="bullets">
    <li>A mindset of self-belief and increased confidence.</li>
    <li>Higher grades and the drive to graduate.</li>
    <li>Social integration and making friends.</li>
    <li>Happiness and fulfilment.</li>
    <li>A deep sense of personal achievement and pride.</li>
  </ul>
</div>

<div class="block have-head"><h2 class="small-head">You Will Have:</h2></div>
<div class="block have-list">
  <ul class="bullets">
    <li>Less stress, knowing that your child is in good hands.</li>
    <li>Fewer sleepless nights worrying about your child.</li>
    <li>Confidence that they are receiving the right support.</li>
    <li>Joy and pride at seeing them do well.</li>
  </ul>
</div>

<div class="block parents-head"><h2 class="small-head">What Parents Say</h2></div>
<div class="block parents-quotes">
  <p class="quote">“Mira was the glue that kept our daughter in college… as our daughter's Academic Coach, [she] gave our daughter the ability to finish strong by empowering her with the skills needed to be successful.”—<cite>Renata</cite></p>
  <p class="quote">“Mira has always told my daughter not that she <em>can</em> succeed, but that she <em>will</em> succeed.”—<cite>Lorraine</cite></p>
</div>

<div class="block students-head"><h2 class="small-head">What Students Say</h2></div>
<div class="block students-quotes">
  <p class="quote"><em>"Last semester I completed all 16 hours and I had the highest GPA I've ever had!" —Former student</em></p>
  <p class="quote">“Under her instruction, my grades began to improve. I ended up making the Dean's List during my time at Westbrook, and I was also inducted into Theta Kappa Rho. I am currently in my first year of law school at Harlow State University, a top tier school.”—<cite>Former student</cite></p>
</div>

<section class="block next-steps">
  <svg class="next-chevron" width="22" height="16" viewBox="0 0 22 16" fill="none" stroke="#ffffff" stroke-width="1.2">
    <polyline points="1,1 8,8 1,15"/><polyline points="11,1 18,8 11,15"/>
  </svg>
  <h3>Next Steps</h3>
  <p>To learn more and discuss your child's individual needs, call <strong>555·014·2297</strong> or email <strong>coach@miraellsworth.net</strong></p>
</section>

<footer class="block footer">www.miraellsworth.net</footer>
</body>
</html>
```